Fresh, modern, fun business card for pediatric dental practice

Need a business card for fresh, modern, fun pediatric dental practice

Clean look that matches our website's font and colors

We prefer the look of curved corners on business cards

Target Market(s)

parents (mothers) of young children, professionals, mid-high class

Industry/Entity Type

Dental

Contact Information for Business Card

Maplebrook Pediatric Dentistry
482 Quarry Lane
Suite 517
Alderton, PA 17590
717.555.0193
www.maplebrookkidsdental.example

Mei-Ran Tsai, DMD
Corinne Walbeck, DMD
(we are working on our email address, but we would like that on the card as well)

Font styles to use
Sans Serif

Requirements
Must have
• All info; we would also like to make cards for individual staff members
• colors from our website and color palatte, attatched
• use same font and design as website for branding
Nice to have
• clean, simple card that has a pop of color
• we would like to see a few designs with our tag line "where smiles get brighter"
• we are not sure if we want to have it on there or not
• we would like to see a few designs incorporating the ribbon graphic on our website where the word WELCOME is

```html
<!DOCTYPE html>
<html lang="en">
<head>
<meta charset="utf-8">
<title>Maplebrook Pediatric Dentistry – Business Card</title>
<link rel="stylesheet" href="https://fonts.googleapis.com/css2?family=Raleway:wght@500;700&family=Lato:wght@400&family=Ubuntu:wght@400;700&display=swap">
<style>
  :root {
    --backdrop: #6e6e6e;
    --card-light: #f3f3f3;
    --card-dark: #2b2b2b;
    --card-dark-tone: #343434;
    --sun-yellow: #f5b921;
    --berry: #c8168c;
    --ink: #2a2a2a;
    --rule: #8c8c8c;
  }
  * { margin: 0; padding: 0; box-sizing: border-box; }
  html, body { width: 1200px; height: 900px; overflow: hidden; }
  body { background: var(--backdrop); position: relative; font-family: "Lato", sans-serif; }

  .card {
    position: absolute;
    top: 184px;
    width: 302px;
    height: 491px;
    border-radius: 13px;
    overflow: hidden;
  }
  .card--front { left: 299px; background: var(--card-light); text-align: center; color: var(--ink); }
  .card--back { left: 646px; background: var(--card-dark); text-align: center; }

  .doctor {
    position: absolute; left: 0; right: 0;
    font-family: "Raleway", sans-serif; font-weight: 500; font-size: 20.5px;
  }
  .doctor--first { top: 91px; color: var(--sun-yellow); }
  .doctor--second { top: 125px; color: var(--berry); }

  .divider { position: absolute; left: 64px; width: 172px; height: 22px; }

  .contact-line { position: absolute; left: 0; right: 0; font-size: 15.5px; line-height: 22px; }
  .phone { top: 209px; }
  .emails { top: 272px; font-size: 15px; }
  .practice-name { top: 356px; color: var(--sun-yellow); font-size: 16px; }
  .address { top: 377px; }

  .back-pattern { position: absolute; inset: 0; background: linear-gradient(160deg, var(--card-dark-tone), var(--card-dark) 70%); }
  .brand-mark { position: absolute; left: 137px; top: 282px; width: 28px; height: 28px; border-radius: 50%; background: var(--sun-yellow); }
  .brand-name {
    position: absolute; left: 0; right: 0; top: 334px;
    font-family: "Ubuntu", sans-serif; font-weight: 700; font-size: 40px; letter-spacing: 1px;
    color: var(--sun-yellow); line-height: 1;
  }
  .brand-tagline {
    position: absolute; left: 0; right: 0; top: 385px;
    font-family: "Ubuntu", sans-serif; font-weight: 400; font-size: 21px; letter-spacing: 1.5px;
    color: var(--berry); line-height: 1;
  }
  .website {
    position: absolute; left: 0; right: 0; top: 439px;
    font-family: "Raleway", sans-serif; font-weight: 700; font-size: 14px; color: var(--sun-yellow);
  }
  .website .domain { color: var(--berry); }
</style>
</head>
<body>

<section class="card card--front" aria-label="Card front with contact details">
  <p class="doctor doctor--first">Mei-Ran Tsai, DMD</p>
  <p class="doctor doctor--second">Corinne Walbeck, DMD</p>

  <svg class="divider" style="top:180px" viewBox="0 0 172 22" aria-hidden="true">
    <line x1="0" y1="11" x2="75" y2="11" stroke="var(--rule)" stroke-width="1"/>
    <line x1="97" y1="11" x2="172" y2="11" stroke="var(--rule)" stroke-width="1"/>
    <circle cx="86" cy="11" r="10" fill="none" stroke="var(--sun-yellow)" stroke-width="1.6"/>
    <path d="M82.2 6.6c.8-.6 1.6-.4 2 .3l.9 1.6c.3.6.1 1.1-.4 1.5l-.6.4c.5 1.3 1.4 2.3 2.6 2.9l.5-.5c.4-.5 1-.6 1.5-.2l1.5 1c.6.4.7 1.2.1 1.9-.7.8-1.7 1.1-2.7.7-2.6-1-4.6-3-5.5-5.6-.4-1.1 0-2.1.1-4z" fill="var(--sun-yellow)"/>
  </svg>
  <p class="contact-line phone">717.555.0193</p>

  <svg class="divider" style="top:246px" viewBox="0 0 172 22" aria-hidden="true">
    <line x1="0" y1="11" x2="75" y2="11" stroke="var(--rule)" stroke-width="1"/>
    <line x1="97" y1="11" x2="172" y2="11" stroke="var(--rule)" stroke-width="1"/>
    <circle cx="86" cy="11" r="10" fill="none" stroke="var(--sun-yellow)" stroke-width="1.6"/>
    <rect x="80.5" y="7.5" width="11" height="7.5" rx="1" fill="var(--sun-yellow)"/>
    <path d="M80.8 8l5.2 4 5.2-4" fill="none" stroke="var(--card-light)" stroke-width="1"/>
  </svg>
  <p class="contact-line emails">Mei-ran@maplebrookkidsdental.example<br>Corinne@maplebrookkidsdental.example</p>

  <svg class="divider" style="top:327px" viewBox="0 0 172 22" aria-hidden="true">
    <line x1="0" y1="11" x2="75" y2="11" stroke="var(--rule)" stroke-width="1"/>
    <line x1="97" y1="11" x2="172" y2="11" stroke="var(--rule)" stroke-width="1"/>
    <circle cx="86" cy="11" r="10" fill="none" stroke="var(--sun-yellow)" stroke-width="1.6"/>
    <path d="M86 17c-2.5-3-4-5.2-4-7.2a4 4 0 0 1 8 0c0 2-1.5 4.2-4 7.2z" fill="var(--sun-yellow)"/>
    <circle cx="86" cy="9.8" r="1.5" fill="var(--card-light)"/>
  </svg>
  <p class="contact-line practice-name">Maplebrook Pediatric Dentistry</p>
  <p class="contact-line address">482 Quarry Lane<br>Suite 517&nbsp; Alderton, PA 17590</p>
</section>

<section class="card card--back" aria-label="Card back with practice name">
  <div class="back-pattern" role="img" aria-label="Subtle repeating sun-swirl pattern on dark background"></div>
  <span class="brand-mark" aria-hidden="true"></span>
  <p class="brand-name">maplebrook</p>
  <p class="brand-tagline">pediatric dentistry</p>
  <p class="website">www.<span class="domain">maplebrookkidsdental</span>.example</p>
</section>

</body>
</html>
```